Brightmill Data Works

Our company is about IT hardwares and IT solutions. IT hardware such as PC, RAMS, storage and servers. IT solutions such as project management, BA. We are also selling new technology too.

Target Market(s)

Consumer, Small to Medium Business, Corporate

Requirements
Must have
• The business card must have the following:
• Name:
• Title:
• Contact Number:
• Email address:
• Website:
• Color: Must match the logo color upgrade

```html
<!DOCTYPE html>
<html lang="en">
<head>
<meta charset="utf-8">
<title>Brightmill Data Works – Business Card</title>
<link rel="stylesheet" href="https://fonts.googleapis.com/css2?family=Titillium+Web:wght@400;600;700&display=swap">
<style>
  :root {
    --stage: #e9e6e1;
    --card-black: #0b0b0b;
    --card-charcoal: #2a2724;
    --accent: #d98a2b;
    --orange-light: #e39a3a;
    --orange-deep: #c9652a;
    --text-light: #f4f1ec;
    --shadow: rgba(0, 0, 0, 0.28);
  }
  * { box-sizing: border-box; margin: 0; padding: 0; }
  html, body {
    width: 1200px; height: 950px; overflow: hidden;
    background: var(--stage);
    font-family: "Titillium Web", sans-serif;
  }
  .canvas { position: relative; width: 1200px; height: 950px; }

  .card {
    position: absolute;
    width: 600px; height: 343px;
    border-radius: 4px;
    box-shadow: 0 14px 30px var(--shadow);
    overflow: hidden;
  }

  /* Front */
  .card-front {
    left: 70px; top: 120px;
    background: linear-gradient(135deg, var(--card-charcoal) 0%, var(--card-black) 55%, var(--card-black) 100%);
    color: var(--text-light);
  }
  .card-front .sheen {
    position: absolute; left: 330px; top: -40px;
    width: 260px; height: 420px;
    background: rgba(255, 255, 255, 0.03);
    transform: rotate(18deg);
  }
  .front-content {
    position: absolute; left: 150px; top: 62px;
    display: flex; flex-direction: column; align-items: center;
    width: 340px; text-align: center;
  }
  .lockup { display: flex; align-items: center; gap: 12px; margin-bottom: 34px; }
  .lockup-square { width: 22px; height: 22px; background: var(--accent); }
  .lockup-name {
    font-weight: 700; font-size: 27px; letter-spacing: 0.5px;
    color: var(--text-light); text-transform: uppercase; line-height: 1;
  }
  .person-name {
    font-weight: 400; font-size: 25px; letter-spacing: 1px;
    text-transform: uppercase; line-height: 1.1;
  }
  .person-title {
    font-weight: 600; font-size: 14px; color: var(--accent);
    text-transform: uppercase; letter-spacing: 0.5px; margin-bottom: 26px;
  }
  .contact-line { font-weight: 600; font-size: 14px; line-height: 1.5; }
  .contact-line .divider { margin: 0 4px; }

  /* Back */
  .card-back {
    left: 530px; top: 500px;
    background: linear-gradient(120deg, var(--orange-light) 0%, var(--orange-deep) 100%);
    color: var(--text-light);
  }
  .card-back .sheen {
    position: absolute; right: -60px; top: -80px;
    width: 300px; height: 300px;
    background: rgba(255, 255, 255, 0.06);
    transform: rotate(20deg);
  }
  .back-website {
    position: absolute; left: 26px; top: 50%;
    transform-origin: left center;
    transform: translate(0, -50%) rotate(90deg) translate(-50%, -50%);
    font-weight: 600; font-size: 14px; letter-spacing: 3px; white-space: nowrap;
  }
  .back-lockup {
    position: absolute; left: 50%; top: 50%;
    transform: translate(-50%, -50%);
    display: flex; align-items: center; gap: 12px;
  }
  .back-lockup .lockup-square { background: var(--text-light); }
  .back-lockup .lockup-name { font-size: 24px; }
</style>
</head>
<body>
<main class="canvas">
  <section class="card card-front" aria-label="Business card front">
    <div class="sheen"></div>
    <div class="front-content">
      <div class="lockup">
        <span class="lockup-square"></span>
        <span class="lockup-name">Brightmill Data Works</span>
      </div>
      <p class="person-name">Daniel Reyes</p>
      <p class="person-title">CEO/Founder</p>
      <p class="contact-line">555 214 8836<span class="divider">|</span>daniel@brightmilldata.com</p>
      <p class="contact-line">www.brightmilldata.com</p>
    </div>
  </section>

  <section class="card card-back" aria-label="Business card back">
    <div class="sheen"></div>
    <p class="back-website">www.brightmilldata.com</p>
    <div class="back-lockup">
      <span class="lockup-square"></span>
      <span class="lockup-name">Brightmill Data Works</span>
    </div>
  </section>
</main>
</body>
</html>
```